Upstart Retirement Planning Firm needs help with business card design

Harborview Nest Advisors, LLC is looking for help with business card design. We give advice on investments, insurance, and other financial matters related to retirement. There are some required disclosures that we will provide but mostly we are looking for a professional, classy business card that reflects the theme we have chosen. We have a logo that is attached but we would like to add a phrase; "Turning Your Earned Income Into Retirement Income"

Doubled sided only so that we can add the required disclosures (needed for our industry) on the back of the card. We will provide the exact words for this in 1-2 days.

Target Market(s)

Retirees and Pre-retirees. Professionals 50+ years old

Industry/Entity Type

Financial Planning

Contact Information for Business Card

We currently have two people who will need separate cards so we'd like to have a template so that we can add names for new cards in the future.

For the first run, please show the following information.

Gregor Pelham, MBA, ChFC®, CLU®
Financial Advisor, Registered Representative
gpelham@harborviewnest.example
Phone: (555) 318-2946
Toll Free Fax: (800) 555-0193

Address is
2187 Meadowlark Ridge Rd.
Suite K418
Virginia Beach, VA 23999

Colors
3277b5

Requirements
Must have
• Logo, contact info, small phase to describe business (in description), required legal disclosures on back of the card as follows (in small font)
• Gregor Pelham is a registered representative of and offers securities through Brightmoor Capital Brokerage Corporation, Member FNQX. Brightmoor Capital Brokerage Corporation is a member of the Brightmoor Capital Alliance which is the marketing name for Brightmoor Holding Corporation and its affiliates.
Nice to have
• Rounded edges, raised letters
Should not have
• any colors that aren't in the logo (other than black for font)

```html
<!DOCTYPE html>
<html lang="en">
<head>
<meta charset="utf-8">
<title>Harborview Nest Advisors – Business Card</title>
<link rel="stylesheet" href="https://fonts.googleapis.com/css2?family=Source+Sans+3:wght@400;600;700&display=swap">
<style>
  :root {
    --backdrop-top: #2b2b2b;
    --backdrop-bottom: #050505;
    --card-white: #ffffff;
    --brand-blue: #1f4a96;
    --card-blue: #2a5aa0;
    --brand-blue-deep: #1d467f;
    --text-grey: #7a7a7a;
  }
  * { margin: 0; padding: 0; box-sizing: border-box; }
  html, body { width: 1200px; height: 900px; overflow: hidden; }
  body {
    position: relative;
    background: linear-gradient(180deg, var(--backdrop-top) 0%, var(--backdrop-bottom) 100%);
    font-family: "Source Sans 3", "Myriad Pro", Arial, sans-serif;
  }
  .card {
    position: absolute;
    top: 306px;
    height: 271px;
    border-radius: 12px;
  }
  .card-front { left: 149px; width: 439px; background: var(--card-white); }
  .card-back { left: 608px; width: 441px; background: var(--card-blue); }

  .brand-block {
    position: absolute;
    left: 18px;
    top: 72px;
    width: 196px;
    text-align: center;
  }
  .brand-name {
    color: var(--brand-blue);
    font-weight: 600;
    font-size: 19px;
    line-height: 22px;
  }
  .tagline {
    margin-top: 22px;
    color: var(--brand-blue);
    font-size: 13px;
    line-height: 16px;
  }

  .contact-block {
    position: absolute;
    left: 224px;
    top: 48px;
    width: 210px;
    color: var(--text-grey);
    font-size: 12.5px;
    line-height: 15.5px;
  }
  .person-name {
    color: var(--brand-blue);
    font-weight: 600;
    font-size: 17px;
    line-height: 20px;
  }
  .credentials { font-size: 11.5px; font-weight: 600; }
  .role { margin-left: 2px; }
  .address { margin-top: 13px; }
  .contact-lines { margin-top: 12px; }
  .contact-line { display: flex; align-items: center; gap: 6px; margin-left: 2px; }
  .contact-line svg { width: 9px; height: 9px; fill: var(--brand-blue); flex: none; }
  .fax {
    margin-top: 9px;
    margin-left: 2px;
    color: var(--brand-blue);
    font-weight: 600;
    font-size: 14px;
  }

  .back-brand {
    position: absolute;
    inset: 0;
    display: flex;
    align-items: center;
    justify-content: center;
    text-align: center;
    color: var(--brand-blue-deep);
    font-weight: 600;
    font-size: 40px;
    line-height: 46px;
  }
</style>
</head>
<body>
  <section class="card card-front">
    <div class="brand-block">
      <div class="brand-name">Harborview Nest<br>Advisors, LLC</div>
      <p class="tagline">Turning Your Earned Income Into<br>Retirement Income</p>
    </div>
    <div class="contact-block">
      <div class="person-name">Gregor Pelham, <span class="credentials">MBA, ChFC®, CLU®</span></div>
      <div class="role">Financial Advisor<br>Registered Representative</div>
      <div class="address">2187 Meadowlark Ridge Rd.<br>Suite K418<br>Virginia Beach, VA 23999</div>
      <div class="contact-lines">
        <div class="contact-line">
          <svg viewBox="0 0 10 10" aria-hidden="true"><path d="M2.2 0.5 L3.8 2.6 L2.9 3.6 Q4 5.9 6.4 7.1 L7.4 6.2 L9.5 7.8 L8.4 9.4 Q4.5 9.4 2.2 6.9 Q0.4 4.6 0.6 1.6 Z"/></svg>
          <span>(555) 318-2946</span>
        </div>
        <div class="contact-line">
          <svg viewBox="0 0 10 10" aria-hidden="true"><path d="M0.5 2 H9.5 V8 H0.5 Z M0.5 2 L5 5.5 L9.5 2" fill="var(--brand-blue)" stroke="#fff" stroke-width="0.8"/></svg>
          <span>gpelham@harborviewnest.example</span>
        </div>
      </div>
      <div class="fax">Toll Free Fax: (800) 555-0193</div>
    </div>
  </section>

  <section class="card card-back">
    <div class="back-brand">Harborview Nest<br>Advisors, LLC</div>
  </section>
</body>
</html>
```